Veltrano.co - Polar Expeditions Specialists

We need a modern, visually striking business card for Veltrano.co, a company specialized in selling expedition cruises to the most remote regions on Earth, with a focus on the Arctic and Antarctica. The design should instantly communicate that the cardholder is an expert in polar travel. Use clean, premium aesthetics with cool tones like icy blue and white, possibly incorporating polar imagery (ice, glaciers, penguins, etc.)

Attached the logo

Contact Information for Business Card

Feels high-end and trustworthy.. Visually memorable — encourages people to keep it

Colors
0054AA
0677BA
7BADD7
CADEEF
E8F1F8

Requirements
Must have
• ice, glaciers, penguins, montains
Nice to have
• modern, transparente,

```html
<!DOCTYPE html>
<html lang="en">
<head>
<meta charset="utf-8">
<title>Veltrano.co Business Card</title>
<link rel="stylesheet" href="https://fonts.googleapis.com/css2?family=Poppins:wght@400;500;600;700&display=swap">
<style>
  :root {
    --page-bg: #e8f1f8;
    --card-blue: #3576b6;
    --ink-white: #ffffff;
    --brand-blue: #2f6fb3;
    --foil-light: #f6f3f3;
    --foil-mid: #e4dcdc;
    --foil-edge: #d2c6c8;
    --dot-line: #4a7fbb;
  }
  * { margin: 0; padding: 0; box-sizing: border-box; }
  html, body {
    width: 1200px; height: 900px; overflow: hidden;
    background: var(--page-bg);
    font-family: "Poppins", sans-serif;
  }
  .business-card {
    position: absolute; left: 100px; top: 141px;
    width: 1000px; height: 618px;
    background: var(--card-blue);
    color: var(--ink-white);
    box-shadow: 0 18px 40px rgba(0, 40, 90, 0.18);
  }
  .holder { position: absolute; left: 40px; top: 80px; }
  .holder-name { font-size: 42px; font-weight: 600; line-height: 1.1; letter-spacing: 0.3px; }
  .holder-role { font-size: 29px; font-weight: 400; line-height: 1.1; }
  .contact-list { position: absolute; left: 40px; top: 288px; list-style: none; }
  .contact-item {
    display: flex; align-items: center; gap: 12px;
    font-size: 29px; line-height: 36px; font-weight: 400;
  }
  .contact-icon { width: 26px; height: 26px; flex: none; }
  .address { position: absolute; left: 42px; top: 478px; font-size: 29px; line-height: 36px; }
  .brand-seal {
    position: absolute; left: 455px; top: 64px;
    width: 496px; height: 496px; border-radius: 50%;
    background: radial-gradient(circle at 38% 30%, var(--foil-light) 0%, var(--foil-mid) 55%, var(--foil-edge) 100%);
  }
  .seal-ring { position: absolute; inset: 0; }
  .brand-name {
    position: absolute; left: 0; right: 0; top: 266px;
    text-align: center; color: var(--brand-blue);
    font-size: 66px; font-weight: 700; line-height: 1;
  }
  .brand-tagline {
    position: absolute; left: 0; right: 0; top: 356px;
    text-align: center; color: var(--brand-blue);
    font-size: 24px; font-weight: 500;
  }
  .brand-mark {
    position: absolute; left: 198px; top: 110px;
    width: 100px; height: 100px; border-radius: 50%;
    background: var(--brand-blue);
  }
</style>
</head>
<body>
  <main class="business-card">
    <header class="holder">
      <h1 class="holder-name">Marcus Hale</h1>
      <p class="holder-role">Managing Director</p>
    </header>

    <ul class="contact-list">
      <li class="contact-item">
        <svg class="contact-icon" viewBox="0 0 24 24" fill="none" stroke="#fff" stroke-width="2" stroke-linecap="round" stroke-linejoin="round"><path d="M22 16.9v3a2 2 0 0 1-2.2 2 19.8 19.8 0 0 1-8.6-3.1 19.5 19.5 0 0 1-6-6A19.8 19.8 0 0 1 2.1 4.2 2 2 0 0 1 4.1 2h3a2 2 0 0 1 2 1.7c.1 1 .4 1.9.7 2.8a2 2 0 0 1-.5 2.1L8 9.9a16 16 0 0 0 6 6l1.3-1.3a2 2 0 0 1 2.1-.4c.9.3 1.8.6 2.8.7a2 2 0 0 1 1.8 2z"/></svg>
        055-987 210 436
      </li>
      <li class="contact-item">
        <svg class="contact-icon" viewBox="0 0 24 24"><rect x="1" y="5" width="22" height="14" fill="#fff"/><path d="M1 5l11 8 11-8" fill="none" stroke="#3576b6" stroke-width="1.8"/></svg>
        hello@veltrano.co
      </li>
      <li class="contact-item">
        <svg class="contact-icon" viewBox="0 0 24 24" fill="none" stroke="#fff" stroke-width="1.8"><circle cx="12" cy="12" r="10"/><path d="M2 12h20M12 2a15 15 0 0 1 0 20M12 2a15 15 0 0 0 0 20"/></svg>
        www.veltrano.co
      </li>
    </ul>

    <address class="address" style="font-style:normal">
      421, Address line goes here<br>45452,Country Name
    </address>

    <section class="brand-seal">
      <svg class="seal-ring" viewBox="0 0 496 496">
        <circle cx="248" cy="248" r="240" fill="none" stroke="var(--dot-line)" stroke-width="2" stroke-dasharray="2 4"/>
      </svg>
      <span class="brand-mark" aria-hidden="true"></span>
      <p class="brand-name">Veltrano.co</p>
      <p class="brand-tagline">Polar Expeditions Specialists</p>
    </section>
  </main>
</body>
</html>
```